Quillmarsh Property Solutions need a business card design

Hello guys. We would need a business card design asap please.
We are a start up property investment business based in London UK specialised in buying, selling, managing and letting properties and helping distressed property owners.
The name of our Business is Quillmarsh, the logo symbolises the four fundamental elements of the world (earth, air, fire and water) and so it stands for strength, stability, longevity.
We would like the business card to communicate professionalism and reliability. Many many thanks indeed for your work.

Details:

1.) Rosalind Updike
Property Investor
Mobile: +44(0)7700123456
Email: rosalind.quillmarsh@mailbox-example.com

2.) Dominic Updike
Property Investor
Mobile: +44(0)7700987654
Email: dominic.quillmarsh@mailbox-example.com

```html
<!DOCTYPE html>
<html lang="en">
<head>
<meta charset="utf-8">
<title>Quillmarsh Property Solutions – Business Card</title>
<link rel="stylesheet" href="https://fonts.googleapis.com/css2?family=Montserrat:wght@700&family=Open+Sans:wght@400;600&display=swap">
<style>
  :root {
    --page-bg: #ece9e4;
    --card-bg: #ffffff;
    --ink-dark: #1b1b1b;
    --ink-grey: #6a6a6a;
    --ink-faint: #a3a3a3;
    --brand-blue: #1f5bc4;
    --brand-green: #22b04b;
    --on-green: #ffffff;
    --shadow: rgba(0, 0, 0, 0.18);
  }
  * { box-sizing: border-box; margin: 0; padding: 0; }
  html, body {
    width: 1200px;
    height: 720px;
    overflow: hidden;
    background: var(--page-bg);
  }
  .canvas {
    position: relative;
    width: 1200px;
    height: 720px;
  }
  .card {
    position: absolute;
    width: 560px;
    height: 320px;
    background: var(--card-bg);
    box-shadow: 0 6px 18px var(--shadow);
    overflow: hidden;
  }
  .card--front { left: 50px; top: 60px; }
  .card--back  { left: 590px; top: 340px; }

  /* Front */
  .wordmark {
    position: absolute;
    left: 0; right: 0;
    top: 92px;
    text-align: center;
    font-family: "Montserrat", sans-serif;
    font-weight: 700;
    color: var(--ink-dark);
    line-height: 1.1;
  }
  .wordmark__name { font-size: 34px; letter-spacing: 1px; }
  .wordmark__tag  { font-size: 13px; letter-spacing: 1px; margin-top: 4px; }

  .holder {
    position: absolute;
    left: 0; right: 0;
    top: 196px;
    text-align: center;
    font-family: "Open Sans", sans-serif;
    font-size: 17px;
  }
  .holder__name { color: var(--brand-blue); font-weight: 600; }
  .holder__role { color: var(--ink-grey); font-weight: 400; font-size: 15px; }

  .rule {
    position: absolute;
    left: 0; right: 0;
    top: 244px;
    height: 2px;
    background: var(--brand-blue);
  }
  .contact-band {
    position: absolute;
    left: 0; right: 0;
    top: 250px;
    height: 70px;
    background: var(--brand-green);
    display: flex;
    align-items: center;
    justify-content: center;
    gap: 28px;
    font-family: "Open Sans", sans-serif;
    font-size: 14px;
    color: var(--on-green);
  }
  .contact-item { display: flex; align-items: center; gap: 7px; }
  .contact-item svg { width: 15px; height: 15px; fill: var(--on-green); }

  /* Back */
  .back-mark {
    position: absolute;
    left: 0; right: 0;
    top: 88px;
    text-align: center;
    font-family: "Montserrat", sans-serif;
    font-weight: 700;
    color: var(--ink-faint);
    line-height: 1.1;
  }
  .back-mark__name { font-size: 50px; letter-spacing: 1px; }
  .back-mark__tag  { font-size: 24px; letter-spacing: 1px; margin-top: 6px; }

  .website {
    position: absolute;
    left: 0; right: 0;
    top: 252px;
    text-align: center;
    font-family: "Open Sans", sans-serif;
    font-size: 18px;
    letter-spacing: 1px;
    color: var(--ink-dark);
  }
</style>
</head>
<body>
<main class="canvas">

  <section class="card card--front" aria-label="Business card front">
    <div class="wordmark">
      <div class="wordmark__name">QUILLMARSH</div>
      <div class="wordmark__tag">PROPERTY SOLUTIONS</div>
    </div>
    <p class="holder">
      <span class="holder__name">Rosalind Updike,</span>
      <span class="holder__role">Property Investor</span>
    </p>
    <div class="rule"></div>
    <div class="contact-band">
      <span class="contact-item">
        <svg viewBox="0 0 16 16" aria-hidden="true"><path d="M4 1h8a1 1 0 0 1 1 1v12a1 1 0 0 1-1 1H4a1 1 0 0 1-1-1V2a1 1 0 0 1 1-1zm1 2v8h6V3H5zm3 9.2a.9.9 0 1 0 0 1.8.9.9 0 0 0 0-1.8z"/></svg>
        +44(0)7700123456
      </span>
      <span class="contact-item">
        <svg viewBox="0 0 16 16" aria-hidden="true"><path d="M1 4h14v9H1V4zm1.5 1.2v.3L8 9l5.5-3.5v-.3H2.5z"/></svg>
        rosalind.quillmarsh@mailbox-example.com
      </span>
    </div>
  </section>

  <section class="card card--back" aria-label="Business card back">
    <div class="back-mark">
      <div class="back-mark__name">QUILLMARSH</div>
      <div class="back-mark__tag">PROPERTY SOLUTIONS</div>
    </div>
    <p class="website">www.quillmarsh-example.com</p>
  </section>

</main>
</body>
</html>
```